Business Card Design - ChoiceCraft

Looking for creative, modern design, two sided for ChoiceCraft that is consistent with color and feel of website www.choicecraftpro.net.
Updates

Back of card will be used to promote products or have a quote revolving around decisions, change, leadership, innovation, creativity. Back should also have space to promote website, but optional to use the icon. Front of the card will need to use the icon and have standard place for name, job title, phone and email. We are not looking to put a mailing address or fax. Also want space to place a few words/phrase explaining what we do...such as individual growth and organizational development or tools, training, information...in addition, want the facebook icon small on the front somewhere as we are also on facebook.

Vector file uploaded of icon.

Target Market(s)

Professional coaching for individual growth and organizational development

Industry/Entity Type

Business

Requirements
Must have
• Icon...see attached.

```html
<!DOCTYPE html>
<html lang="en">
<head>
<meta charset="utf-8">
<title>ChoiceCraft Business Card</title>
<link rel="stylesheet" href="https://fonts.googleapis.com/css2?family=Tinos:wght@400;700&family=Arimo:wght@400;700&display=swap">
<style>
  :root {
    --stage: #e4e6e8;
    --card-white: #ffffff;
    --brand-blue: #1677bf;
    --brand-deep: #0c5fa8;
    --brand-sky: #2fa6e0;
    --brand-pale: #8fd0f2;
    --ink: #3a3a3a;
    --ink-soft: #555a5f;
    --rule: #b9bcc0;
  }
  * { margin: 0; padding: 0; box-sizing: border-box; }
  html, body { width: 1200px; height: 1071px; overflow: hidden; }
  body { background: var(--stage); position: relative; font-family: "Tinos", serif; }

  .card { position: absolute; width: 797px; height: 454px; overflow: hidden; box-shadow: 0 2px 8px rgba(0,0,0,.25); }

  /* Front */
  .card-front { left: 67px; top: 61px; background: var(--card-white); }
  .front-swoosh { position: absolute; inset: 0; }
  .holder { position: absolute; right: 40px; top: 28px; text-align: right; color: #fff; }
  .holder-name { font-weight: 700; font-size: 31px; line-height: 1.1; }
  .holder-title { font-size: 24px; line-height: 1.1; }
  .brand { position: absolute; left: 36px; top: 179px; display: flex; align-items: center; gap: 20px; }
  .brand-dot { width: 126px; height: 126px; border-radius: 50%; background: radial-gradient(circle at 40% 35%, #e6eef5, #9db4c8); }
  .brand-name { font-weight: 700; font-size: 37px; color: var(--brand-blue); }
  .contacts { position: absolute; left: 36px; top: 331px; list-style: none; font-size: 20px; color: var(--ink); }
  .contacts li { display: flex; align-items: center; gap: 8px; height: 24.5px; }
  .contacts svg { width: 14px; height: 14px; flex: none; }
  .fb-square { width: 13px; height: 13px; background: #3b5a9a; flex: none; }
  .divider { position: absolute; left: 297px; top: 356px; width: 1px; height: 75px; background: var(--rule); }
  .mission { position: absolute; left: 318px; top: 365px; font-size: 19px; line-height: 22px; color: var(--ink-soft); }

  /* Back */
  .card-back { left: 336px; top: 553px; background: radial-gradient(ellipse at 85% 85%, #3ab2ea 0%, #1f8ad0 45%, #1370bb 100%); color: #fff; font-family: "Arimo", sans-serif; }
  .brand-mark-faint { position: absolute; left: 561px; top: 263px; width: 180px; height: 180px; border-radius: 50%; background: radial-gradient(circle at 40% 35%, rgba(255,255,255,.55), rgba(170,220,245,.35)); }
  .quotes { position: absolute; left: 55px; top: 38px; list-style: none; }
  .quote { position: relative; padding-left: 27px; height: 80px; }
  .quote-text { font-size: 19px; line-height: 26px; }
  .quote-text::after { content: "\201D"; font-family: "Tinos", serif; font-weight: 700; font-size: 38px; line-height: 0; position: relative; top: 14px; margin-left: 3px; }
  .quote::before { content: "\201C"; position: absolute; left: 0; top: -4px; font-family: "Tinos", serif; font-weight: 700; font-size: 38px; line-height: 1; }
  .quote-author { font-size: 19px; font-weight: 700; line-height: 26px; margin-top: 6px; }
</style>
</head>
<body>

<section class="card card-front" aria-label="Card front">
  <svg class="front-swoosh" viewBox="0 0 797 454" aria-hidden="true">
    <defs>
      <linearGradient id="swoosh-fill" x1="0" y1="0" x2="1" y2="0.4">
        <stop offset="0" stop-color="#2f9fdc"/>
        <stop offset="1" stop-color="#0c5fa8"/>
      </linearGradient>
    </defs>
    <path d="M40,10 C260,-10 560,70 797,230 L797,246 C560,90 260,8 40,10 Z" fill="#8fd0f2"/>
    <path d="M300,0 C470,40 650,120 797,212 L797,0 Z" fill="url(#swoosh-fill)"/>
    <path d="M250,40 C470,80 660,170 797,280 L797,250 C650,150 470,72 250,40 Z" fill="#2fa6e0"/>
  </svg>

  <div class="holder">
    <p class="holder-name">Your Name</p>
    <p class="holder-title">Title</p>
  </div>

  <div class="brand">
    <span class="brand-dot"></span>
    <span class="brand-name">ChoiceCraft</span>
  </div>

  <ul class="contacts">
    <li><svg viewBox="0 0 14 14"><circle cx="7" cy="7" r="6" fill="none" stroke="#444" stroke-width="1.2"/><path d="M4.5 4 L6 4 L6.5 6 L5.6 6.6 Q6.4 8.2 7.6 8.6 L8.2 7.6 L10 8.2 L10 9.6 Q6 10 4.5 4 Z" fill="#444"/></svg>123-456-789</li>
    <li><svg viewBox="0 0 14 14"><rect x="1.5" y="3.5" width="11" height="8" fill="#444"/><path d="M1.5 3.5 L7 8 L12.5 3.5" fill="none" stroke="#fff" stroke-width="1"/></svg>hello@choicecraftpro.net</li>
    <li><svg viewBox="0 0 14 14"><circle cx="7" cy="7" r="5.5" fill="none" stroke="#444" stroke-width="1.2"/><ellipse cx="7" cy="7" rx="2.4" ry="5.5" fill="none" stroke="#444" stroke-width="1"/><path d="M1.5 7 H12.5" stroke="#444" stroke-width="1"/></svg>www.choicecraftpro.net</li>
    <li><span class="fb-square"></span>/choicecraftpro</li>
  </ul>

  <span class="divider"></span>
  <p class="mission">Supporting individual growth<br>and organizational development<br>or tools, training, information</p>
</section>

<section class="card card-back" aria-label="Card back">
  <span class="brand-mark-faint"></span>
  <ul class="quotes">
    <li class="quote"><p class="quote-text">Try not to become a man of success, but rather a man of value.</p><p class="quote-author">- Alden Marsh</p></li>
    <li class="quote"><p class="quote-text">The only constant is change.</p><p class="quote-author">- Theron Vale</p></li>
    <li class="quote"><p class="quote-text">We are what we repeatedly do. Excellence is not an act, it is a habit.</p><p class="quote-author">- Corwin Hale</p></li>
    <li class="quote"><p class="quote-text">Simplicity is the ultimate sophistication.</p><p class="quote-author">- Lorenzo Brevi</p></li>
    <li class="quote"><p class="quote-text">Life is not fair - get used to it.</p><p class="quote-author">- Wes Harlan</p></li>
  </ul>
</section>

</body>
</html>
```